Website design for an Italian restaurant in Amsterdam

I need a design for a client of mine. It is for Teatro Lucerna, an Italian restaurant in Amsterdam.
We are going for a clean, modern look but we also need to realise an authentic feel.
The restaurant is located in an old movie theatre, that is where the name Teatro Lucerna comes from.
Industry/Entity Type
Italian Restaurant
Number of Pages Required
1 page
Font styles to use
Sans Serif
Colors
Designer to choose colors to be used in the design.

```html
<!DOCTYPE html>
<html lang="en">
<head>
<meta charset="utf-8">
<title>Teatro Lucerna – Ristorante Italiano</title>
<link rel="stylesheet" href="https://fonts.googleapis.com/css2?family=Lusitana:wght@400;700&family=Lato:wght@400;700&display=swap">
<style>
:root{
  --red:#a3001e;
  --red-dark:#7c0016;
  --black:#050505;
  --ink:#333;
  --muted:#555;
  --white:#fff;
  --footer-bar:#2b2b2b;
  --serif:"Lusitana", Georgia, serif;
  --sans:"Lato", Arial, sans-serif;
}
*{box-sizing:border-box;margin:0;padding:0}
html,body{width:1200px;height:3543px;overflow:hidden;background:var(--white);font-family:var(--sans);color:var(--ink)}
.page{position:relative;width:1200px;height:3543px;overflow:hidden}
.abs{position:absolute}

/* header */
.site-header{position:absolute;left:0;top:0;width:1200px;height:98px;background:var(--black);display:flex;align-items:center;padding:0 125px;z-index:5}
.brand{display:flex;align-items:center;gap:12px;color:var(--white);font-family:var(--serif);font-size:21px;letter-spacing:1px;text-transform:uppercase}
.brand-dot{width:30px;height:30px;border-radius:50%;background:var(--red)}
.brand small{display:block;font-family:var(--sans);font-size:9px;color:#999;letter-spacing:1px;text-transform:none}
.main-nav{display:flex;gap:34px;margin-left:46px;font-family:var(--serif);font-size:15px;color:#ddd;text-transform:uppercase}
.main-nav .active{color:var(--white)}
.header-phone{margin-left:auto;display:flex;align-items:center;gap:8px;color:var(--white);font-size:16px}

/* hero */
.hero{position:absolute;left:0;top:98px;width:1200px;height:720px;background:radial-gradient(ellipse at 40% 40%,#5a3a22 0%,#2d1c12 45%,#0d0907 100%)}
.hero-title{position:absolute;top:210px;width:1200px;text-align:center;color:var(--white);font-family:var(--serif);text-transform:uppercase}
.hero-title .small{font-size:48px;letter-spacing:1px}
.hero-title .big{font-size:64px;letter-spacing:2px;line-height:1}
.btn-outline{position:absolute;border:2px solid var(--white);border-radius:30px;color:var(--white);font-weight:700;font-size:15px;text-align:center;text-transform:uppercase}
.arrow{position:absolute}

/* menu band */
.menu-band{position:absolute;left:0;top:745px;width:1200px;height:448px}
.section-title{font-family:var(--serif);text-transform:uppercase;text-align:center;font-size:30px;letter-spacing:1px}
.title-rule{width:60px;height:2px;margin:8px auto 0;background:currentColor;opacity:.7}
.menu-cards{position:absolute;left:127px;top:873px;display:flex;gap:5px}
.menu-card{position:relative;width:231px;height:249px;background:linear-gradient(160deg,#4a3a30,#1c1512);color:var(--white);text-align:center}
.menu-card:nth-child(2){background:linear-gradient(160deg,#6a6258,#2a2420)}
.menu-card:nth-child(3){background:linear-gradient(160deg,#7a3a24,#2a1510)}
.menu-card:nth-child(4){background:linear-gradient(160deg,#3e4a34,#18140f)}
.menu-card h3{position:absolute;top:105px;width:100%;font-family:var(--serif);font-size:21px;font-weight:400;text-transform:uppercase}
.menu-card p{position:absolute;top:135px;left:25px;right:25px;font-size:11px;line-height:1.3;color:#ddd}
.menu-card .more{position:absolute;left:100px;top:189px;width:30px;height:30px;border:1.5px solid var(--white);border-radius:50%}

/* welcome */
.welcome{position:absolute;left:0;top:1193px;width:1200px;height:495px}
.welcome-text{position:absolute;left:140px;top:96px;width:420px;text-align:center}
.welcome-text .kicker{font-family:var(--serif);font-size:28px;color:#444;text-transform:uppercase}
.welcome-text .name{font-family:var(--serif);font-size:36px;color:var(--red);text-transform:uppercase;line-height:1.1}
.welcome-text p{font-size:15.5px;line-height:1.7;color:var(--muted);margin-top:14px}
.btn-red{display:inline-block;margin-top:26px;background:var(--red);color:var(--white);border-radius:30px;width:170px;height:52px;line-height:52px;font-weight:700;font-size:15px;text-transform:uppercase}

/* reservation */
.reservation{position:absolute;left:0;top:1688px;width:1200px;height:434px;background:linear-gradient(100deg,#0e1a2e 0%,#1d3550 35%,#131a24 60%,#090b10 100%);color:var(--white);text-align:center}
.reservation h2{position:absolute;top:118px;width:100%;font-family:var(--serif);font-weight:400;font-size:36px;text-transform:uppercase}
.reservation p{position:absolute;top:174px;left:250px;width:700px;font-size:17px;line-height:1.55}

/* group menu */
.group-title{position:absolute;top:2180px;width:1200px;color:var(--red)}
.group-card{position:absolute;top:2265px;height:285px;color:var(--white);text-align:center}
.group-card .frame{position:absolute;inset:10px;border:1.5px solid rgba(255,255,255,.85)}
.group-card h3{position:absolute;top:112px;width:100%;font-family:var(--serif);font-weight:400;font-size:24px;text-transform:uppercase}
.group-card .price{position:absolute;top:142px;width:100%;font-family:var(--serif);font-size:30px}

/* top menu */
.top-title{position:absolute;left:127px;top:2622px;font-family:var(--serif);font-size:34px;color:var(--red-dark);text-transform:uppercase}
.dish{position:absolute;left:132px;display:flex;gap:28px}
.dish-img{width:124px;height:124px;border-radius:50%;background:radial-gradient(circle,#8a5a3a,#3a2418)}
.dish h4{font-size:19px;font-weight:400;color:var(--red-dark);margin-top:10px}
.dish p{font-size:14.5px;line-height:1.6;color:var(--muted);width:390px;margin-top:4px}
.dish a{font-weight:700;color:var(--ink);font-size:14.5px;text-decoration:none}

.feed{position:absolute;left:720px;top:2625px;width:348px;height:350px;background:var(--white);border:1px solid #ccc;box-shadow:0 1px 4px rgba(0,0,0,.2);font-size:11px;color:#333}
.feed-head{height:48px;background:linear-gradient(90deg,#222,#555);color:var(--white);padding:8px 12px;font-weight:700;font-size:13px}
.feed-post{margin:12px 14px;padding-bottom:10px;border-bottom:1px solid #e4e4e4}
.feed-post .who{display:flex;align-items:center;gap:8px;font-weight:700}
.feed-post .who span{width:26px;height:26px;background:#333;display:inline-block}
.feed-post p{margin-top:8px;line-height:1.4}
.feed-post .link{color:#4a67a8;margin-top:4px}
.feed-foot{position:absolute;bottom:0;left:0;right:0;height:28px;border-top:1px solid #ddd;text-align:center;line-height:28px;color:#555}

/* footer */
.footer{position:absolute;left:0;top:3020px;width:1200px;height:455px}
.footer-brand{position:absolute;left:150px;top:190px;width:220px;text-align:center;color:var(--white);font-family:var(--serif);font-size:21px;text-transform:uppercase}
.footer-brand .dot{width:40px;height:40px;border-radius:50%;background:var(--red);margin:0 auto 12px}
.footer-brand small{display:block;font-family:var(--sans);font-size:9px;color:#888;text-transform:none;letter-spacing:1px}
.social{display:flex;gap:10px;justify-content:center;margin-top:18px}
.social span{width:34px;height:34px;border:1.5px solid var(--white);border-radius:50%}
.footer-col{position:absolute;top:178px;color:var(--white)}
.footer-col h5{font-family:var(--serif);font-weight:400;font-size:18px;text-transform:uppercase;margin-bottom:16px}
.footer-col li{list-style:none;font-size:13.5px;line-height:28px;color:#ddd;text-transform:uppercase}
.footer-col.plain li{text-transform:none}
.copyright{position:absolute;left:0;top:3475px;width:1200px;height:68px;background:var(--footer-bar);color:#bbb;font-size:13px;text-align:center;line-height:68px}
</style>
</head>
<body>
<div class="page">

  <header class="site-header">
    <div class="brand"><span class="brand-dot"></span><div>Teatro Lucerna<small>Ristorante Italiano</small></div></div>
    <nav class="main-nav"><span class="active">Home</span><span>Menu</span><span>Groupmenu</span><span>Reservation</span><span>Contact</span></nav>
    <div class="header-phone">
      <svg width="18" height="18" viewBox="0 0 24 24"><path fill="#c8102e" d="M6.6 10.8a15 15 0 006.6 6.6l2.2-2.2c.3-.3.7-.4 1-.2 1.1.4 2.3.6 3.6.6.6 0 1 .4 1 1V20c0 .6-.4 1-1 1A17 17 0 013 4c0-.6.4-1 1-1h3.5c.6 0 1 .4 1 1 0 1.3.2 2.5.6 3.6.1.3 0 .7-.2 1z"/></svg>
      (+31) 20 555 0182
    </div>
  </header>

  <section class="hero" role="img" aria-label="Candle-lit dining room of the restaurant with booths and set tables">
    <div class="hero-title"><div class="small">Welcome to</div><div class="big">Teatro Lucerna</div></div>
    <div class="btn-outline" style="left:510px;top:345px;width:186px;height:56px;line-height:52px">View Menu</div>
    <svg class="arrow" style="left:80px;top:292px" width="30" height="60"><path d="M26 4 4 30l22 26" stroke="#fff" stroke-width="2" fill="none"/></svg>
    <svg class="arrow" style="left:1088px;top:292px" width="30" height="60"><path d="M4 4l22 26L4 56" stroke="#fff" stroke-width="2" fill="none"/></svg>
  </section>

  <svg class="menu-band" viewBox="0 0 1200 448" preserveAspectRatio="none"><path d="M0 40Q600-40 1200 40V448H0Z" fill="var(--red)"/></svg>
  <div class="abs section-title" style="top:795px;width:1200px;color:#fff">Our Menu<div class="title-rule"></div></div>
  <svg class="arrow" style="left:88px;top:965px" width="24" height="44"><path d="M20 4 4 22l16 18" stroke="#fff" stroke-width="4" fill="none"/></svg>
  <svg class="arrow" style="left:1072px;top:965px" width="24" height="44"><path d="M4 4l16 18L4 40" stroke="#fff" stroke-width="4" fill="none"/></svg>
  <div class="menu-cards">
    <article class="menu-card" role="img" aria-label="Plate of antipasti"><h3>Antipasti</h3><p>Morbi ornare gravida elit integer congue augue et malesuada</p><span class="more"></span></article>
    <article class="menu-card" role="img" aria-label="Fresh salad with wine glass"><h3>Le Insalate</h3><p>Morbi ornare gravida elit integer congue augue et malesuada</p><span class="more"></span></article>
    <article class="menu-card" role="img" aria-label="Pasta dish with tomatoes"><h3>Le Paste</h3><p>Morbi ornare gravida elit integer congue augue et malesuada</p><span class="more"></span></article>
    <article class="menu-card" role="img" aria-label="Fish dish with greens"><h3>Il Pesce</h3><p>Morbi ornare gravida elit integer congue augue et malesuada</p><span class="more"></span></article>
  </div>

  <section class="welcome">
    <div class="welcome-text">
      <div class="kicker">Welcome to</div>
      <div class="name">Teatro Lucerna</div>
      <p>Fusce ultricies orci ac feugiat suscipit leo massa sodales velit et scelerisque mi tortor at</p>
      <p>gravida elit Integer congue augue et malesuada iaculis ipsum dui aliquet felis at cursus magna nisl nec elit Praesent elementum elit at tellus nec ultr</p>
      <span class="btn-red">Learn More</span>
    </div>
    <svg class="abs" style="left:575px;top:0" width="625" height="495" role="img" aria-label="Theatre dining hall with a ring of lights and a cinema screen"><defs><radialGradient id="hall" cx="55%" cy="30%" r="80%"><stop offset="0" stop-color="#6a4a2a"/><stop offset=".5" stop-color="#2a1a10"/><stop offset="1" stop-color="#0a0705"/></radialGradient></defs><path d="M80 0H625V495H70Q-60 247 80 0Z" fill="url(#hall)"/></svg>
  </section>

  <section class="reservation" role="img" aria-label="Large illuminated aquarium in the dim restaurant">
    <h2>Reservation</h2>
    <p>gravida elit Integer congue augue et malesuada iaculis ipsum dui aliquet felis at cursus magna nisl nec elit Praesent elementum elit at tellus</p>
    <div class="btn-outline" style="left:518px;top:248px;width:156px;height:52px;line-height:48px;font-size:14px">Click Here</div>
  </section>

  <div class="group-title section-title">Group Menu<div class="title-rule"></div></div>
  <div class="group-card" role="img" aria-label="Pan of pasta on a wooden table" style="left:127px;width:471px;background:linear-gradient(150deg,#5a4432,#241a12)"><span class="frame"></span><h3>Groupmenu Speciale</h3><div class="price">€ 34,50</div></div>
  <div class="group-card" role="img" aria-label="Guests sharing a plated dish" style="left:610px;width:472px;background:linear-gradient(150deg,#3a3030,#14100e)"><span class="frame"></span><h3>Groupmenu Royal</h3><div class="price">€ 49,50</div></div>

  <h2 class="top-title">Top Menu</h2>
  <div class="dish" style="top:2700px"><div class="dish-img" role="img" aria-label="Plated main course"></div><div><h4>Anim In massa libero interdum</h4><p>nec interdum vel blandit sed nulla in ullamcorper est eget tempor cursus neque mi consectetuer mi a ultricies</p><a>Click here</a></div></div>
  <div class="dish" style="top:2858px"><div class="dish-img" role="img" aria-label="Plated dessert" style="background:radial-gradient(circle,#d8a050,#5a3418)"></div><div><h4>Curabitur vel mi sit amet</h4><p>nec interdum vel blandit sed nulla in ullamcorper est eget tempor cursus neque mi consectetuer</p><a>Click here</a></div></div>

  <aside class="feed">
    <div class="feed-head">Teatro Lucerna<br><span style="font-weight:400;font-size:10px">Page updates</span></div>
    <div class="feed-post"><div class="who"><span></span>Teatro Lucerna</div><p>Verse pasta vandaag, kom en proef de specialiteiten van onze nieuwe chef...</p><div class="link">See Translation</div><p style="color:#777">11 · Comment · 1</p></div>
    <div class="feed-post"><div class="who"><span></span>Teatro Lucerna</div><p>Nieuw... kom ook privé dineren, in de private dining van ons theater Teatro Lucerna...</p><div class="link">See Translation</div><p style="color:#777">12 · 2 · 1</p></div>
    <div class="feed-foot">Find us online</div>
  </aside>

  <svg class="abs" style="left:0;top:2835px" width="1200" height="230" role="img" aria-label="Faint line drawing of canal houses skyline"><rect x="0" y="0" width="1200" height="230" fill="url(#sky)"/><defs><linearGradient id="sky" x1="0" y1="0" x2="0" y2="1"><stop offset="0" stop-color="#fff"/><stop offset="1" stop-color="#ececec"/></linearGradient></defs></svg>

  <svg class="footer" viewBox="0 0 1200 455" preserveAspectRatio="none"><path d="M0 40Q600-40 1200 40V455H0Z" fill="var(--black)"/></svg>
  <div class="abs" style="left:0;top:3020px;width:1200px;height:455px">
    <div class="footer-brand"><div class="dot"></div>Teatro Lucerna<small>Ristorante Italiano</small>
      <div class="social"><span aria-label="Social link"></span><span aria-label="Social link"></span><span aria-label="Social link"></span><span aria-label="Social link"></span></div>
    </div>
    <div class="footer-col" style="left:440px"><h5>Quick Links</h5><ul><li>Home</li><li>Menu</li><li>Groupmenu</li><li>Reservation</li><li>Contact</li></ul></div>
    <div class="footer-col plain" style="left:637px"><h5>Today Our Menu</h5><ul><li>Orata al Pistacchio</li><li>Filetto di Manzo al Gorgonzola</li><li>Melanzana alla Parmigiana</li></ul></div>
    <div class="footer-col" style="left:892px"><h5>Contact Us</h5><ul><li>Teatro Lucerna</li><li>Keizerslaan 42</li><li>1016AB Amsterdam</li><li>Tel nr: (+31) 20 555 0182</li></ul></div>
  </div>
  <footer class="copyright">© 2018 Company Name. All right reserved</footer>

</div>
</body>
</html>
```